International business needs business cards

Our company, DRV Ventures Inc. is in the business of supplying a range construction products with particular emphasis on CEMENT. We have developed our own brand - TORVAN SUPPLIES - with which to infiltrate the market. We are launching our brand of cement (TORVAN Type IS Cement) into the Caribbean which is unlike anything this market has ever seen. A monopoly has existed here for the past 60-odd years and the market has now opened to allow the importation of other brands and consumers are anxious and ready for change/improvement. We are very excited to be launching and want to make a great first impression. We will be conducting workshops and seminars (from government level to the hardware store owners) and we want our business card to give us the strong, confident introduction that we need.

Target Market(s)

construction; builders; engineers; home owners

Industry/Entity Type

Construction

Contact Information for Business Card

Marisol Depree
CEO
cell # 1 555 4180736
Ground floor,Lindell Plaza Suite 2734
George Town,Grand Cayman
Cayman Islands,KY1-4823
EMAIL: m.depree@drvventuresinc.example
web site drvventuresinc.example

COMPANY: skype info drv.ventures.example

second card
Yvette Brannock-Depree
CFO
CELL# 1 555 607 3941
George Town,Grand Cayman
Cayman Islands,KY1-4823
EMAIL: y.brannockdepree@drvventuresinc.example
website drvventuresinc.example

Requirements
Must have
• Business cards must display BOTH logos - DRV is the company and TORVAN is the brand.

```html
<!DOCTYPE html>
<html lang="en">
<head>
<meta charset="utf-8">
<title>DRV Ventures Inc. – Business Card</title>
<link rel="stylesheet" href="https://fonts.googleapis.com/css2?family=Open+Sans:wght@400;600;700&display=swap">
<style>
  :root {
    --stage: #3a3a3a;
    --card: #ffffff;
    --ink: #111111;
    --band: #0c0c0c;
    --brand-red: #8e1b1f;
    --crest-dark: #2a2a2a;
    --crest-mid: #8a8a8a;
    --icon-red: #b4232a;
  }
  * { box-sizing: border-box; margin: 0; padding: 0; }
  html, body { width: 1200px; height: 900px; overflow: hidden; }
  body {
    background: var(--stage);
    font-family: "Open Sans", Arial, sans-serif;
    color: var(--ink);
    position: relative;
  }
  .card {
    position: absolute;
    width: 560px;
    height: 320px;
    background: var(--card);
    border-radius: 22px;
    overflow: hidden;
    box-shadow: 0 14px 30px rgba(0,0,0,0.45);
  }

  /* Front: brand side */
  .card-front { left: 60px; top: 90px; }
  .brand-crest {
    position: absolute;
    left: 170px; top: 40px;
    width: 220px; height: 190px;
    border-radius: 12px;
    background: radial-gradient(ellipse at center, var(--crest-mid) 0%, var(--crest-dark) 70%);
    display: flex; align-items: center; justify-content: center;
  }
  .brand-name {
    font-weight: 700;
    font-size: 30px;
    letter-spacing: 3px;
    color: #ffffff;
  }
  .front-handle {
    position: absolute;
    left: 0; right: 0; top: 258px;
    display: flex; align-items: center; justify-content: center; gap: 7px;
    font-size: 15px; font-weight: 600;
  }
  .handle-dot {
    width: 12px; height: 12px; border-radius: 50%;
    background: var(--icon-red);
  }

  /* Back: company contact side */
  .card-back { left: 580px; top: 480px; }
  .company-mark {
    position: absolute;
    right: 36px; top: 34px;
    display: flex; align-items: center; gap: 12px;
  }
  .company-square {
    width: 74px; height: 74px;
    background: var(--brand-red);
  }
  .company-name {
    font-weight: 700;
    font-size: 26px;
    line-height: 1.05;
    color: var(--ink);
  }
  .name-band {
    position: absolute;
    left: 0; right: 0; top: 146px;
    height: 70px;
    background: var(--band);
    color: #ffffff;
  }
  .person {
    position: absolute;
    right: 36px; top: 8px;
    text-align: right;
  }
  .person-name {
    font-weight: 700; font-size: 25px; letter-spacing: 0.5px;
    text-transform: uppercase;
  }
  .person-role { font-size: 11px; font-weight: 600; }
  .band-square {
    position: absolute;
    left: 28px; top: 16px;
    width: 38px; height: 38px;
    border: 3px solid #ffffff;
  }
  .address {
    position: absolute;
    left: 28px; top: 232px;
    font-size: 13px; font-weight: 700; line-height: 1.45;
  }
  .contacts {
    position: absolute;
    right: 28px; top: 232px;
    list-style: none;
    font-size: 13px; font-weight: 600; line-height: 1.45;
  }
  .contacts li { display: flex; align-items: center; gap: 6px; }
  .contacts svg { width: 11px; height: 11px; flex: none; }
</style>
</head>
<body>

<section class="card card-front" aria-label="Brand side">
  <div class="brand-crest" role="img" aria-label="Heraldic crest with crown, crossed swords and laurel wreath for the TORVAN brand">
    <span class="brand-name">TORVAN</span>
  </div>
  <p class="front-handle"><span class="handle-dot"></span>drv.ventures.example</p>
</section>

<section class="card card-back" aria-label="Contact side">
  <div class="company-mark">
    <span class="company-square"></span>
    <span class="company-name">DRV<br>VENTURES INC.</span>
  </div>

  <div class="name-band">
    <span class="band-square"></span>
    <div class="person">
      <p class="person-name">Marisol Depree</p>
      <p class="person-role">CEO</p>
    </div>
  </div>

  <address class="address" style="font-style:normal">
    Ground floor,Lindell Plaza Suite 2734<br>
    George Town,Grand Cayman<br>
    Cayman Islands,KY1-4823
  </address>

  <ul class="contacts">
    <li>
      <svg viewBox="0 0 12 12"><path d="M3 1l2 2.5-1.2 1.3a6 6 0 0 0 3.4 3.4L8.5 7 11 9l-1.2 2C5 11 1 7 1 2.2z" fill="var(--icon-red)"/></svg>
      1 555 4180736
    </li>
    <li>
      <svg viewBox="0 0 12 12"><rect x="1" y="2.5" width="10" height="7" fill="none" stroke="var(--icon-red)" stroke-width="1.3"/><path d="M1 2.5l5 4 5-4" fill="none" stroke="var(--icon-red)" stroke-width="1.3"/></svg>
      m.depree@drvventuresinc.example
    </li>
    <li>
      <svg viewBox="0 0 12 12"><circle cx="6" cy="6" r="5" fill="none" stroke="var(--icon-red)" stroke-width="1.3"/><path d="M1 6h10M6 1c2.5 3 2.5 7 0 10M6 1c-2.5 3-2.5 7 0 10" fill="none" stroke="var(--icon-red)" stroke-width="1"/></svg>
      www.drvventuresinc.example
    </li>
  </ul>
</section>

</body>
</html>
```